RB Halden Electric Yard Sign

Looking to have a yard sign designed that we can place at projects we are working on. Most likely will be 18" H x 24" W but flexible that we can increase the size if necessary. It should include our logo, our phone # 609-555-0147, website rbhaldenelectric.example and slogan, built on integrity, driven by excellence. Colors should match our brand.

```html
<!DOCTYPE html>
<html lang="en">
<head>
<meta charset="UTF-8">
<title>RB Halden Electric Yard Sign</title>
<link href="https://fonts.googleapis.com/css2?family=Roboto:wght@400;700;900&display=swap" rel="stylesheet">
<style>
  :root {
    --backdrop: #8c8c8c;
    --sign-white: #ffffff;
    --brand-red: #e3222b;
    --brand-navy: #1d2f63;
    --text-white: #ffffff;
  }
  * { box-sizing: border-box; margin: 0; padding: 0; }
  html, body {
    width: 684px;
    height: 1200px;
    overflow: hidden;
  }
  body {
    background: var(--backdrop);
    font-family: "Roboto", Arial, sans-serif;
    display: flex;
    align-items: center;
    justify-content: center;
  }
  .yard-sign {
    width: 620px;
    height: 470px;
    background: var(--sign-white);
    display: flex;
    flex-direction: column;
    box-shadow: 0 6px 16px rgba(0,0,0,0.25);
  }
  .sign-brand {
    height: 250px;
    display: flex;
    align-items: center;
    justify-content: center;
    gap: 18px;
  }
  .brand-mark {
    width: 30px;
    height: 30px;
    background: var(--brand-red);
  }
  .brand-name {
    font-weight: 900;
    font-size: 56px;
    letter-spacing: 1px;
    color: var(--brand-navy);
    text-transform: uppercase;
  }
  .sign-slogan {
    height: 105px;
    background: var(--brand-red);
    color: var(--text-white);
    display: flex;
    flex-direction: column;
    justify-content: center;
    align-items: center;
    font-weight: 700;
    font-size: 36px;
    line-height: 1.1;
    text-transform: uppercase;
    text-align: center;
  }
  .sign-contact {
    flex: 1;
    background: var(--brand-navy);
    color: var(--text-white);
    display: flex;
    flex-direction: column;
    justify-content: center;
    align-items: center;
  }
  .contact-phone {
    font-weight: 900;
    font-size: 58px;
    line-height: 1;
    letter-spacing: 1px;
  }
  .contact-web {
    font-weight: 400;
    font-size: 20px;
    margin-top: 8px;
  }
</style>
</head>
<body>
  <main class="yard-sign">
    <header class="sign-brand">
      <span class="brand-mark" aria-hidden="true"></span>
      <span class="brand-name">RB Halden Electric</span>
    </header>
    <section class="sign-slogan">
      <p>Built on integrity,</p>
      <p>driven by excellence.</p>
    </section>
    <footer class="sign-contact">
      <p class="contact-phone">609-555-0147</p>
      <p class="contact-web">www.rbhaldenelectric.example</p>
    </footer>
  </main>
</body>
</html>
```